Silver Bloom Marisol's Cleaning Service Business Cards Project

A business card with all contact details with logo design on there (already have a logo) eye catching Logo and contact info on one side, full logo on the back, must target upper class residential and corporate companies, fitness companies, still keep it on the feminine side of things , must look elegant

Target Market(s)

Upper class homes and corporate companies

Industry/Entity Type

Cleaning Service

Contact Information for Business Card

Name: Marisol Quenby
Position: Director
ABN: 31647209853
Email: marisolssilvercleaning@tidymail.example
Number: 0417906354

Font styles to use
Decorative

Colors

Designer to choose colors to be used in the design.

Requirements
Must have
• Available Sydney Wide, contact info and logo on one side, full logo on the back
Nice to have
• Professional appearance
Should not have
• Cheap advert looking stuff

```html
<!DOCTYPE html>
<html lang="en">
<head>
<meta charset="utf-8">
<title>Silver Bloom – Business Cards</title>
<link rel="stylesheet" href="https://fonts.googleapis.com/css2?family=Lora:wght@500&family=Roboto:wght@400;500&display=swap">
<style>
  :root {
    --backdrop: #e9e7e3;
    --front-dark: #1a1b1d;
    --back-slate: #2b2f3b;
    --aqua-pale: #98fdf7;
    --aqua: #2de3d8;
    --aqua-text: #3fe3d6;
    --white: #ffffff;
    --muted-rule: #5a5d63;
    --ghost: #3a4a55;
  }
  * { box-sizing: border-box; margin: 0; padding: 0; }
  html, body { width: 1200px; height: 960px; overflow: hidden; }
  body { background: var(--backdrop); position: relative; font-family: "Roboto", Arial, sans-serif; }

  .card { position: absolute; width: 600px; height: 342px; overflow: hidden; box-shadow: 0 4px 12px rgba(0,0,0,.25); }
  .card--front { left: 314px; top: 114px; background: var(--front-dark); }
  .card--back { left: 312px; top: 472px; height: 343px; background: var(--back-slate); }

  .card__bands { position: absolute; inset: 0; }

  .brand { position: absolute; text-align: center; }
  .brand__name { font-family: "Lora", Georgia, serif; font-weight: 500; color: var(--aqua-text); text-transform: uppercase; white-space: nowrap; }
  .brand__tagline { color: var(--white); text-transform: uppercase; white-space: nowrap; }

  .card--front .brand { left: 40px; top: 205px; width: 250px; }
  .card--front .brand__mark { width: 14px; height: 14px; border-radius: 50%; background: var(--aqua-text); margin: 0 auto 10px; }
  .card--front .brand__name { font-size: 21px; letter-spacing: .5px; }
  .card--front .brand__tagline { font-size: 8px; letter-spacing: 2px; margin-top: 4px; }

  .divider { position: absolute; left: 267px; top: 86px; width: 1px; height: 172px; background: var(--muted-rule); }

  .contact { position: absolute; left: 297px; top: 98px; color: var(--white); }
  .contact__name { font-size: 21px; font-weight: 500; color: var(--aqua-text); text-transform: uppercase; line-height: 1.1; }
  .contact__role { font-size: 14px; font-weight: 500; color: var(--aqua-text); text-transform: uppercase; margin-top: 2px; }
  .contact__abn { font-size: 14px; margin-top: 16px; }
  .contact__list { list-style: none; margin-top: 11px; }
  .contact__item { display: flex; align-items: center; gap: 8px; font-size: 14px; line-height: 19px; }
  .contact__icon { width: 12px; height: 12px; flex: none; fill: var(--aqua-text); }

  .card--back .brand { left: 45px; top: 86px; width: 270px; }
  .card--back .brand__name { font-size: 27px; letter-spacing: 1px; }
  .card--back .brand__tagline { font-size: 10px; letter-spacing: 2.6px; margin-top: 4px; }
  .card--back .brand__web { color: var(--white); font-size: 14px; letter-spacing: 3px; margin-top: 4px; }

  .emblem-area { position: absolute; left: 365px; top: 12px; width: 210px; height: 190px; background: radial-gradient(circle, rgba(58,74,85,.7), rgba(58,74,85,0) 70%); }
  .flourish-area { position: absolute; left: 175px; top: 208px; width: 425px; height: 120px; background: linear-gradient(90deg, rgba(58,74,85,0), rgba(58,74,85,.55) 30%, rgba(58,74,85,.55) 80%, rgba(58,74,85,.2)); border-radius: 60px 0 0 60px; }
</style>
</head>
<body>

<section class="card card--front" aria-label="Business card front">
  <svg class="card__bands" viewBox="0 0 600 342" aria-hidden="true">
    <polygon points="0,0 600,0 0,58" fill="var(--aqua-pale)"/>
    <polygon points="0,342 600,342 600,283" fill="var(--aqua)"/>
  </svg>

  <div class="brand">
    <div class="brand__mark"></div>
    <p class="brand__name">Silver Bloom</p>
    <p class="brand__tagline">Marisol’s Cleaning Service</p>
  </div>

  <div class="divider"></div>

  <div class="contact">
    <h1 class="contact__name">Marisol Quenby</h1>
    <p class="contact__role">Director</p>
    <p class="contact__abn">ABN: 31647209853</p>
    <ul class="contact__list">
      <li class="contact__item">
        <svg class="contact__icon" viewBox="0 0 24 24"><path d="M6.6 10.8a15.1 15.1 0 0 0 6.6 6.6l2.2-2.2c.3-.3.7-.4 1-.2 1.1.4 2.3.6 3.6.6.6 0 1 .4 1 1V20c0 .6-.4 1-1 1A17 17 0 0 1 3 4c0-.6.4-1 1-1h3.5c.6 0 1 .4 1 1 0 1.3.2 2.5.6 3.6.1.3 0 .7-.2 1z"/></svg>
        0417906354
      </li>
      <li class="contact__item">
        <svg class="contact__icon" viewBox="0 0 24 24"><path d="M2 5h20v14H2z M2 5l10 7 10-7" /><path d="M3 6.5l9 6.3 9-6.3" fill="none" stroke="var(--front-dark)" stroke-width="2"/></svg>
        marisolssilvercleaning@tidymail.example
      </li>
      <li class="contact__item">
        <svg class="contact__icon" viewBox="0 0 24 24"><circle cx="12" cy="12" r="11"/><path d="M3 12h18M12 1c3 3 3 19 0 22M12 1c-3 3-3 19 0 22" fill="none" stroke="var(--front-dark)" stroke-width="1.5"/></svg>
        www.silverbloom.example
      </li>
    </ul>
  </div>
</section>

<section class="card card--back" aria-label="Business card back">
  <div class="emblem-area" role="img" aria-label="Faint large brand emblem decoration"></div>
  <div class="flourish-area" role="img" aria-label="Faint floral scroll ornament"></div>

  <div class="brand">
    <p class="brand__name">Silver Bloom</p>
    <p class="brand__tagline">Marisol’s Cleaning Service</p>
    <p class="brand__web">www.silverbloom.example</p>
  </div>
</section>

</body>
</html>
```